Redesign of business card for Cedar Ridge Mechanical

We are looking for a new design for our business cards for Cedar Ridge Mechanical. We are a plumbing & HVAC construction company, operating on the West Coast of Canada and USA. Logo attached.
Industry/Entity Type
Construction - Plumbing & HVAC
Contact Information for Business Card
Name, address, phone numbers, email, website address
Look and feel
Each slider illustrates characteristics of the customer's brand and the style your logo design should communicate.

```html
<!DOCTYPE html>
<html lang="en">
<head>
<meta charset="UTF-8">
<title>Cedar Ridge Mechanical – Business Card</title>
<link rel="stylesheet" href="https://fonts.googleapis.com/css2?family=Montserrat:wght@400;500;700;800&display=swap">
<style>
  :root {
    --page-bg: #2b2b2d;
    --card-black: #141414;
    --pattern-dark: #1c1c1c;
    --pattern-light: #262626;
    --card-white: #f7f7f7;
    --stripe-grey: #8f8f8f;
    --text-light: #ffffff;
    --text-muted: #d8d8d8;
    --text-dark: #3a3a3a;
    --text-soft: #7a7a7a;
  }
  * { margin: 0; padding: 0; box-sizing: border-box; }
  html, body {
    width: 1200px; height: 963px; overflow: hidden;
    background: var(--page-bg);
    font-family: "Montserrat", sans-serif;
  }
  .business-card {
    position: absolute;
    left: 280px;
    width: 640px; height: 366px;
    border-radius: 22px;
    overflow: hidden;
    background: var(--card-black);
    box-shadow: 0 18px 44px rgba(0,0,0,.45);
  }
  .card-front { top: 74px; }
  .card-back { top: 522px; }

  /* front */
  .card-wave { position: absolute; inset: 0; width: 100%; height: 100%; }
  .holder { position: absolute; left: 44px; top: 36px; color: var(--text-light); }
  .holder-name {
    font-weight: 800; font-size: 21px; letter-spacing: 1.2px; text-transform: uppercase;
  }
  .holder-role { font-weight: 400; font-size: 14px; color: var(--text-muted); margin-top: 2px; }
  .contact { position: absolute; left: 44px; top: 178px; color: var(--text-dark); }
  .contact-address { font-size: 16px; line-height: 1.25; color: var(--text-soft); margin-bottom: 16px; }
  .contact-list { list-style: none; }
  .contact-item { display: flex; align-items: center; gap: 8px; font-size: 16px; line-height: 1.45; }
  .contact-item svg { width: 12px; height: 12px; flex: none; fill: var(--text-dark); }
  .contact-item strong { font-weight: 700; }
  .brand {
    position: absolute; display: flex; align-items: center;
    color: var(--text-light); font-weight: 700; text-transform: uppercase; letter-spacing: 1px;
  }
  .card-front .brand { right: 44px; top: 140px; gap: 14px; }
  .card-front .brand-name { font-size: 23px; line-height: 1.15; }
  .card-front .brand-mark { width: 28px; height: 28px; border-width: 3px; }
  .brand-mark { border: 3px solid var(--text-light); border-radius: 5px; flex: none; }

  /* back */
  .back-pattern {
    position: absolute; inset: 0;
    background: linear-gradient(135deg, var(--pattern-light), var(--pattern-dark) 55%, var(--card-black));
  }
  .card-back .brand { right: 44px; bottom: 40px; gap: 10px; }
  .card-back .brand-name { font-size: 17px; line-height: 1.15; }
  .card-back .brand-mark { width: 20px; height: 20px; border-width: 2px; border-radius: 4px; }
</style>
</head>
<body>
  <article class="business-card card-front">
    <svg class="card-wave" viewBox="0 0 840 480" preserveAspectRatio="none" aria-hidden="true">
      <path d="M0,168 C150,128 300,150 392,290 C470,400 640,430 840,392 L840,404 C640,444 462,414 382,298 C300,178 150,152 0,180 Z" fill="var(--stripe-grey)"/>
      <path d="M0,190 C150,160 290,180 372,300 C455,420 640,452 840,420 L840,480 L0,480 Z" fill="var(--card-white)"/>
      <path d="M0,190 C150,160 290,180 372,300 C455,420 640,452 840,420" fill="none" stroke="var(--card-black)" stroke-width="5"/>
    </svg>

    <header class="holder">
      <h1 class="holder-name">Daniel Brooks</h1>
      <p class="holder-role">Manager</p>
    </header>

    <section class="contact">
      <p class="contact-address">Your address, city<br>state, ZIP 0000</p>
      <ul class="contact-list">
        <li class="contact-item">
          <svg viewBox="0 0 16 16"><path d="M3 1l3 3-2 2c1 2 3 4 5 5l2-2 3 3-2 3C6 15 1 10 0 3z"/></svg>
          123-456-2100
        </li>
        <li class="contact-item">
          <svg viewBox="0 0 16 16"><path d="M1 3h14v10H1z M1 3l7 6 7-6" fill="none" stroke="#3a3a3a" stroke-width="2"/></svg>
          youremail@mailbox.com
        </li>
        <li class="contact-item">
          <svg viewBox="0 0 16 16"><circle cx="8" cy="8" r="7"/></svg>
          <span>www.<strong>yourwebsite</strong>.com</span>
        </li>
      </ul>
    </section>

    <div class="brand">
      <span class="brand-mark"></span>
      <span class="brand-name">Cedar Ridge<br>Mechanical</span>
    </div>
  </article>

  <article class="business-card card-back">
    <div class="back-pattern" role="img" aria-label="Faint repeating company monogram pattern across the black card back"></div>
    <div class="brand">
      <span class="brand-mark"></span>
      <span class="brand-name">Cedar Ridge<br>Mechanical</span>
    </div>
  </article>
</body>
</html>
```